Boutique Shoe Bag Race wear Business Card Design

We are a new luxury shoe bag, jewellery and race wear store stocking local and international designers. Located in the fashion precinct of beautiful Marlow Beach famous in Sydney Australia. Stocking French jewellery and shoes such as Henri Delacrouxs plus Australian made. Looking at quality and service and looking after the locals and tourists.
Ideas: White background, Black writing in bold engravers, logo in middle of Marlow and Boutique a gold horseshoe (facing upright so the curve is at the bottom) with a black stiletto inside. French clover silver and black border (not irish clover the French lattice type look)
Updates

Marlow Atelier

I open 8/4 so require business card design ASAP.

Please place gold horseshoe facing upwards with the black stiletto inside.

Bold engravers writing for business name.

I will have my phone number tomorrow to update.

Border in similar/same style as attached picture with black/silver clover French design.

Thank you. Nina                                   

Industry/Entity Type

Fashion

Contact Information for Business Card

Marlow Atelier
Boutique Owner Nina Pellard
41B Tilbury Lane
Marlow Beach MRL 2940 Australia
0471392605
02 **** *TBA
info@marlowatelier.com.au
Pagefolk.com/MarlowAtelier
www.marlowatelier.com.au

Font styles to use
Other font styles liked:
• Bold Engravers

Requirements
Must have
• Info on one side including business name and logo with black stiletto and gold horse shoe. reverse side with French clover border and Larger name Marlow Atelier with logo in centre.
Should not have
• irish clover
French script
horseshoe upside down

```html
<!DOCTYPE html>
<html lang="en">
<head>
<meta charset="utf-8">
<title>Marlow Atelier – Business Cards</title>
<link rel="stylesheet" href="https://fonts.googleapis.com/css2?family=Cinzel:wght@700&family=Mulish:wght@700&family=Questrial&display=swap">
<style>
  :root {
    --bg: #2b2b2b;
    --card-white: #ffffff;
    --ink: #111111;
    --ink-soft: #222222;
    --lattice-dark: #1c1c1c;
    --lattice-mid: #3a3a3a;
    --silver-light: #d9d9d9;
    --silver-dark: #9a9a9a;
    --gold: #c9a24a;
    --icon-grey: #8a8a8a;
  }
  html, body {
    margin: 0;
    padding: 0;
    width: 1200px;
    height: 1000px;
    overflow: hidden;
    background: var(--bg);
  }
  .canvas {
    position: relative;
    width: 1200px;
    height: 1000px;
  }

  /* Front card */
  .card-front {
    position: absolute;
    left: 33px;
    top: 66px;
    width: 737px;
    height: 430px;
  }
  .lattice-border {
    position: absolute;
    inset: 0;
    background: linear-gradient(135deg, var(--lattice-mid), var(--lattice-dark));
  }
  .front-face {
    position: absolute;
    left: 40px;
    top: 42px;
    width: 657px;
    height: 347px;
    background: var(--card-white);
  }
  .front-wordmark {
    position: absolute;
    left: 0;
    right: 0;
    top: 126px;
    text-align: center;
    font-family: "Cinzel", serif;
    font-weight: 700;
    font-size: 44px;
    letter-spacing: 6px;
    color: var(--ink);
    white-space: nowrap;
  }
  .front-web {
    position: absolute;
    left: 0;
    right: 0;
    top: 286px;
    text-align: center;
    font-family: "Questrial", sans-serif;
    font-size: 22px;
    color: var(--ink-soft);
  }

  /* Back card */
  .card-back {
    position: absolute;
    left: 388px;
    top: 530px;
    width: 740px;
    height: 438px;
    background: linear-gradient(180deg, var(--silver-light), var(--silver-dark) 50%, var(--silver-light));
  }
  .back-face {
    position: absolute;
    left: 15px;
    top: 17px;
    width: 710px;
    height: 405px;
    background: var(--card-white);
  }
  .back-wordmark {
    position: absolute;
    left: 27px;
    top: 64px;
    font-family: "Cinzel", serif;
    font-weight: 700;
    font-size: 34px;
    letter-spacing: 6px;
    color: var(--ink);
    white-space: nowrap;
  }
  .brand-dot {
    position: absolute;
    left: 593px;
    top: 50px;
    width: 60px;
    height: 60px;
    border-radius: 50%;
    background: var(--gold);
  }
  .owner-name {
    position: absolute;
    left: 27px;
    top: 173px;
    font-family: "Mulish", sans-serif;
    font-weight: 700;
    font-size: 30px;
    color: var(--ink);
  }
  .owner-title {
    position: absolute;
    left: 26px;
    top: 220px;
    font-family: "Questrial", sans-serif;
    font-size: 32px;
    color: var(--ink-soft);
  }
  .contact-list {
    position: absolute;
    left: 24px;
    top: 293px;
    margin: 0;
    padding: 0;
    list-style: none;
    font-family: "Questrial", sans-serif;
    font-size: 22px;
    line-height: 29.5px;
    color: var(--ink-soft);
  }
  .contact-list li {
    display: flex;
    align-items: center;
    gap: 4px;
  }
  .contact-icon {
    width: 18px;
    height: 18px;
    flex: none;
  }
  .address {
    position: absolute;
    right: 26px;
    top: 299px;
    text-align: right;
    font-family: "Questrial", sans-serif;
    font-style: normal;
    font-size: 22px;
    line-height: 30px;
    color: var(--ink-soft);
  }
</style>
</head>
<body>
<main class="canvas">

  <section class="card-front">
    <div class="lattice-border" role="img" aria-label="Black and silver French lattice clover border pattern"></div>
    <div class="front-face">
      <div class="front-wordmark">MARLOW ATELIER</div>
      <div class="front-web">www.marlowatelier.com.au</div>
    </div>
  </section>

  <section class="card-back">
    <div class="back-face">
      <div class="back-wordmark">MARLOW ATELIER</div>
      <div class="brand-dot"></div>

      <div class="owner-name">Nina Pellard</div>
      <div class="owner-title">Boutique Owner</div>

      <ul class="contact-list">
        <li>
          <svg class="contact-icon" viewBox="0 0 18 18" aria-hidden="true">
            <rect x="5" y="1.5" width="8" height="15" rx="1.5" fill="none" stroke="var(--icon-grey)" stroke-width="1.2"/>
            <line x1="8" y1="14" x2="10" y2="14" stroke="var(--icon-grey)" stroke-width="1.2"/>
          </svg>
          0471392605 02
        </li>
        <li>
          <svg class="contact-icon" viewBox="0 0 18 18" aria-hidden="true">
            <rect x="1.5" y="4" width="15" height="10" fill="none" stroke="var(--icon-grey)" stroke-width="1.2"/>
            <polyline points="1.5,4 9,10 16.5,4" fill="none" stroke="var(--icon-grey)" stroke-width="1.2"/>
          </svg>
          info@marlowatelier.com.au
        </li>
        <li>
          <svg class="contact-icon" viewBox="0 0 18 18" aria-hidden="true">
            <circle cx="9" cy="9" r="8" fill="var(--icon-grey)"/>
          </svg>
          Pagefolk.com/MarlowAtelier
        </li>
      </ul>

      <address class="address">
        41B Tilbury Lane<br>
        Marlow Beach<br>
        MRL 2940 Australia
      </address>
    </div>
  </section>

</main>
</body>
</html>
```